Business card design

I need my logo on this card, things I need the card to have on it
licensed and insured.
owner operators Milo & Trent Halvorsen
my phone number 5083716254
Disaster Recovery, Storm Damage Restoration, Proactive Disaster Plan Management, Roof Repair/Restoration Structural Repair and Reconstruction, Emergency Boarding and Tarping Service, Perimeter Fencing, Emergency Tree Removal,

```html
<!DOCTYPE html>
<html lang="en">
<head>
<meta charset="utf-8">
<title>Halvorsen's Construction – Business Card</title>
<link rel="stylesheet" href="https://fonts.googleapis.com/css2?family=Questrial&family=Teko:wght@400&display=swap">
<style>
  :root {
    --card-bg: #2c2d42;
    --brand-blue: #1b8fe6;
    --accent-red: #e8283b;
    --text-light: #f2f2f5;
  }
  html, body {
    margin: 0;
    padding: 0;
    width: 1200px;
    height: 685px;
    overflow: hidden;
    background: var(--card-bg);
  }
  .card {
    position: relative;
    width: 1200px;
    height: 685px;
    background: var(--card-bg);
    font-family: "Questrial", "Helvetica Neue", Arial, sans-serif;
    color: var(--text-light);
    text-align: center;
  }
  .brand-mark {
    position: absolute;
    left: 540px;
    top: 78px;
    width: 120px;
    height: 120px;
    background: var(--brand-blue);
  }
  .wordmark {
    position: absolute;
    left: 0;
    right: 0;
    top: 242px;
    color: var(--brand-blue);
    font-weight: 400;
    line-height: 1;
  }
  .wordmark__name {
    display: block;
    font-size: 71px;
    letter-spacing: 0.01em;
  }
  .wordmark__tagline {
    display: block;
    margin-top: 10px;
    font-size: 19px;
    letter-spacing: 0.74em;
    padding-left: 0.74em;
  }
  .owners {
    position: absolute;
    left: 0;
    right: 0;
    top: 382px;
    margin: 0;
    font-family: "Teko", "Arial Narrow", sans-serif;
    font-weight: 400;
    font-size: 78px;
    line-height: 1;
    letter-spacing: 0.1em;
    padding-left: 0.1em;
    color: var(--accent-red);
  }
  .phone {
    position: absolute;
    left: 0;
    right: 0;
    top: 462px;
    margin: 0;
    font-size: 26px;
    line-height: 1.2;
  }
  .phone__label {
    color: var(--accent-red);
    margin-right: 6px;
  }
  .services {
    position: absolute;
    left: 0;
    right: 0;
    top: 537px;
    margin: 0;
    padding: 0;
    list-style: none;
    font-size: 23.8px;
    line-height: 30px;
  }
  .services__sep {
    display: inline-block;
    width: 6px;
    height: 6px;
    margin: 0 8px;
    background: var(--accent-red);
    vertical-align: middle;
    position: relative;
    top: -2px;
  }
</style>
</head>
<body>
  <main class="card">
    <div class="brand-mark" aria-hidden="true"></div>

    <div class="wordmark">
      <span class="wordmark__name">HALVORSEN’S</span>
      <span class="wordmark__tagline">CONSTRUCTION L.L.C</span>
    </div>

    <h1 class="owners">MILO &amp; TRENT HALVORSEN</h1>

    <p class="phone"><span class="phone__label">P:</span>508-371-6254</p>

    <ul class="services">
      <li>Disaster Recovery<span class="services__sep"></span>Perimeter Fencing<span class="services__sep"></span>Emergency Tree Removal</li>
      <li>Structural Repair and Reconstruction<span class="services__sep"></span>Emergency Boarding and Tarping Service</li>
      <li>Roof Repair/Restoration<span class="services__sep"></span>Storm Damage Restoration<span class="services__sep"></span>Proactive Disaster Plan Management</li>
    </ul>
  </main>
</body>
</html>
```